Hospitality project presentation

I am developing a hospitality project and I need to present to the developer an outstanding presentation highlighting the overall look and feel. I will provide the text and most of the pictures (not all of them) some pictures (copyright free) will hae to be provided by the designer. Maximum number of pages 15, and zoom calls with me to make some adjustment if needed.

Hospitality

• calibri light

• 15 slides
• Hospitality resort project look and feel

```html
<!DOCTYPE html>
<html lang="en">
<head>
<meta charset="utf-8">
<title>Hospitality Project Pitch Deck – Slide Overview</title>
<link href="https://fonts.googleapis.com/css2?family=Nunito:wght@400;700;800;900&family=Open+Sans:wght@400;600;700&family=Lora:ital@1&display=swap" rel="stylesheet">
<style>
:root{
  --green:#66b22c;
  --green-dark:#3f7f24;
  --green-soft:#9ed064;
  --panel:#e9efe0;
  --ink:#1b1b1b;
  --body:#3a3a3a;
  --page:#ffffff;
}
*{margin:0;padding:0;box-sizing:border-box}
html,body{width:1200px;height:1200px;overflow:hidden;background:var(--page)}
body{position:relative;font-family:"Open Sans",sans-serif;color:var(--ink)}
.slide{position:absolute;width:305px;height:172px;background:#fff;overflow:hidden;box-shadow:0 4px 10px rgba(0,0,0,.2)}
.abs{position:absolute}
.panel{position:absolute;background:var(--panel)}
.brand{position:absolute;left:26px;top:8px;display:flex;align-items:center;gap:2px;font-family:"Nunito",sans-serif;font-weight:800;font-size:5px;color:var(--green-dark)}
.brand::before{content:"";width:6px;height:6px;border-radius:50%;background:var(--green)}
.brand.right{left:auto;right:16px}
.title{position:absolute;font-family:"Nunito",sans-serif;font-weight:900;font-size:12px;line-height:1.3;color:var(--ink)}
.title .bar,.bar{display:block;width:22px;height:2px;background:var(--green);margin-top:4px}
.txt{position:absolute;font-size:2.7px;line-height:1.4;color:var(--body)}
.txt b{color:var(--ink)}
.lbl{font-family:"Open Sans",sans-serif;font-weight:700;font-size:3.4px;color:var(--ink);display:block;margin-bottom:1px}
.num{font-family:"Nunito",sans-serif;font-weight:900;font-size:8px;color:var(--ink);display:block}
.foot-l,.foot-r{position:absolute;top:161px;font-size:2.4px;color:var(--green)}
.foot-l{left:26px;width:110px;border-bottom:.4px solid #bbb;padding-bottom:1px}
.foot-r{right:16px;width:100px;text-align:right;border-bottom:.4px solid #bbb;padding-bottom:1px}
.icon{width:6px;height:6px;display:inline-block;vertical-align:middle}
.opt{position:absolute;display:flex;gap:4px;align-items:flex-start}
.opt .txt{position:static}
.social{position:absolute;display:flex;gap:5px}
.social span{width:5px;height:5px;border-radius:50%;background:var(--green)}
.ph-pool{background:linear-gradient(180deg,#6fb2d8 0%,#2f7fa8 55%,#7ec3d6 100%)}
.ph-resort{background:linear-gradient(160deg,#3a86b8 0%,#2aa3b3 40%,#5d8a4a 75%,#c9d2c4 100%)}
.ph-palm{background:linear-gradient(180deg,#d8dfe3 0%,#8b9a6a 35%,#4a6a3a 55%,#6fb0c4 100%)}
.ph-deck{background:linear-gradient(180deg,#e8e6df 0%,#a99a7e 45%,#5a3c26 100%)}
.ph-night{background:linear-gradient(180deg,#0d3a8a 0%,#2f6fc4 50%,#1d2c5a 100%)}
.ph-room{background:linear-gradient(135deg,#c8b49a 0%,#8a7460 50%,#e3d8c8 100%)}
.ph-dark{background:linear-gradient(180deg,#2a2e38 0%,#5a4a38 55%,#141414 100%)}
.ph-desk{background:linear-gradient(180deg,#606060 0%,#1d1d1d 100%)}
.ph-beach{background:linear-gradient(180deg,#e8c6a8 0%,#b9c6c4 35%,#3fa3a3 60%,#d9d2c4 100%)}
.ph-person{background:linear-gradient(180deg,#e7e9eb 0%,#b9bec3 45%,#2a2d33 100%)}
.ph-cover{background:linear-gradient(120deg,#4e9a3a 0%,#6fbf3e 45%,#4aa0c8 80%,#2a6f8a 100%)}
.quote{position:absolute;font-family:"Lora",serif;font-style:italic;font-size:6px;line-height:1.25;color:var(--ink)}
svg text{font-family:"Open Sans",sans-serif}
</style>
</head>
<body>

<!-- 01 cover -->
<section class="slide" style="left:100px;top:49px">
  <div class="abs ph-cover" style="inset:0" role="img" aria-label="Aerial view of a tropical resort with palms and sea"></div>
  <div class="abs" style="left:44px;top:-20px;width:210px;height:210px;border-radius:50%;background:rgba(102,178,44,.8)"></div>
  <div class="abs" style="left:36px;top:76px;display:flex;align-items:center;gap:4px;font-family:'Nunito',sans-serif;font-weight:900;font-size:12px;color:#fff">
    <span style="width:16px;height:16px;border-radius:50%;background:#3f7f24"></span>Verdell
  </div>
  <div class="title" style="left:124px;top:42px;color:#fff;font-size:15px;line-height:1.35">Hospitality<br>Project<br>Pitch Deck<span class="bar" style="background:#fff;width:40px"></span></div>
  <div class="abs" style="left:124px;top:115px;font-size:5px;color:#fff;line-height:1.3">YOUR SUBTITLE SLIDE BUSINESS<br>PRESENTATION GOES HERE</div>
  <div class="abs" style="left:130px;top:160px;font-size:2.4px;color:#fff">www.verdellresort.com</div>
</section>

<!-- 02 about company -->
<section class="slide" style="left:451px;top:49px">
  <div class="brand">Verdell</div>
  <div class="title" style="left:29px;top:38px">About Our Company</div>
  <div class="txt" style="left:27px;top:72px;width:65px">Lorem ipsum has been the industry's standard dummy text ever since the 1500s, when an unknown printer took a galley of type and made a specimen book.<br><br><br>Lorem ipsum has been the industry's standard dummy text ever since the 1500s, when an unknown printer took a galley of type and made a specimen book.</div>
  <div class="txt" style="left:105px;top:69px;width:66px"><b>Lorem Ipsum</b> is simply dummy text of the printing and typesetting industry. Lorem ipsum has been the industry's standard dummy text ever since the 1500s, when an unknown printer took a galley of type and scrambled it to make a type specimen book. It has survived not only five centuries, but also the leap into electronic typesetting, remaining essentially unchanged. It was popularised in the 1960s with the release of sheets containing passages, and more recently with desktop publishing software.</div>
  <div class="panel" style="left:184px;top:0;width:121px;height:172px"></div>
  <div class="abs ph-pool" style="left:202px;top:29px;width:86px;height:114px" role="img" aria-label="Infinity pool lined with palm trees reflecting the sky"></div>
  <div class="foot-l">Hospitality project name here</div><div class="foot-r">www.verdellresort.com / 02</div>
</section>

<!-- 03 vision mission -->
<section class="slide" style="left:802px;top:49px">
  <div class="brand">Verdell</div>
  <div class="title" style="left:27px;top:38px">Vision And<br>Mission<span class="bar"></span></div>
  <div class="txt" style="left:27px;top:88px;width:78px"><b>Lorem Ipsum</b> is simply dummy text of the printing and typesetting industry. Lorem ipsum has been the industry's standard dummy text ever since the 1500s, when an unknown printer took a galley of type and scrambled it to make a type specimen book. It has survived not only five centuries, but also the leap into electronic typesetting, remaining essentially unchanged. It was popularised in the 1960s with the release of sheets containing passages, and more recently with desktop publishing software.</div>
  <div class="panel" style="left:118px;top:27px;width:82px;height:65px"></div>
  <div class="txt" style="left:132px;top:48px;width:56px">Lorem ipsum has been the industry's standard dummy text ever since the 1500s, when an unknown printer took a galley of type and scrambled.</div>
  <div class="abs ph-resort" style="left:200px;top:27px;width:105px;height:65px" role="img" aria-label="Resort pool beside the ocean"></div>
  <div class="txt" style="left:132px;top:108px;width:76px"><span class="lbl">Vision</span><br>Lorem ipsum has been the industry's standard dummy text ever since the 1500s, when an unknown printer took a galley of type and scrambled it to make a type specimen book.</div>
  <div class="txt" style="left:215px;top:108px;width:76px"><span class="lbl">Mission</span><br>Lorem ipsum has been the industry's standard dummy text ever since the 1500s, when an unknown printer took a galley of type and scrambled it to make a type specimen book.</div>
  <div class="foot-l">Hospitality project name here</div><div class="foot-r">www.verdellresort.com / 03</div>
</section>

<!-- 04 about project -->
<section class="slide" style="left:100px;top:236px">
  <div class="brand">Verdell</div>
  <div class="abs ph-resort" style="left:27px;top:29px;width:252px;height:67px" role="img" aria-label="Coastal resort with pools and palm trees"></div>
  <div class="title" style="left:29px;top:104px">About the<br>project<span class="bar"></span></div>
  <div class="txt" style="left:104px;top:108px;width:70px"><b>Lorem Ipsum</b> is simply dummy text of the printing and typesetting industry. Lorem ipsum has been the industry's standard dummy text ever since the 1500s, when an unknown printer took a galley of type and made a type specimen book. It has survived not</div>
  <div class="panel" style="left:181px;top:96px;width:99px;height:47px"></div>
  <div class="txt" style="left:194px;top:104px;width:73px"><b>Lorem Ipsum</b> is simply dummy text of the printing and typesetting industry. Lorem ipsum has been the industry's standard dummy text ever since the 1500s, when an unknown printer took a galley of type and made a type specimen book. It has survived not</div>
  <div class="foot-l">Hospitality project name here</div><div class="foot-r">www.verdellresort.com / 04</div>
</section>

<!-- 05 lorem deck -->
<section class="slide" style="left:451px;top:236px">
  <div class="brand right">Verdell</div>
  <div class="abs ph-deck" style="left:26px;top:0;width:103px;height:143px" role="img" aria-label="Wooden deck with sun loungers facing the sea"></div>
  <div class="panel" style="left:129px;top:86px;width:155px;height:65px"></div>
  <div class="title" style="left:147px;top:32px">Lorem Ipsum is<br>simply dummy text<span class="bar"></span></div>
  <div class="txt" style="left:145px;top:96px;width:120px"><b>Lorem Ipsum is simply dummy text</b></div>
  <div class="txt" style="left:145px;top:107px;width:60px">Lorem ipsum has been the industry's standard dummy text ever since the 1500s, when an unknown printer took a galley of type and scrambled it to make a type specimen book.</div>
  <div class="txt" style="left:215px;top:107px;width:60px">Lorem ipsum has been the industry's standard dummy text ever since the 1500s, when an unknown printer took a galley of type and scrambled it to make a type specimen book.</div>
  <div class="foot-l">Hospitality project name here</div><div class="foot-r">www.verdellresort.com / 05</div>
</section>

<!-- 06 break slide -->
<section class="slide" style="left:802px;top:236px">
  <div class="abs ph-pool" style="left:0;top:0;width:202px;height:172px" role="img" aria-label="Pool with palm trees and umbrellas at sunset"></div>
  <div class="brand right">Verdell</div>
  <div class="abs" style="left:143px;top:23px;width:136px;height:126px;background:rgba(233,239,224,.88)"></div>
  <div class="title" style="left:167px;top:58px">Break Slide</div>
  <div class="quote" style="left:165px;top:90px;width:90px">“Business opportunities are like buses, there's always another one coming.”<br><span style="padding-left:40px">– Elena Marsh.</span></div>
  <div class="foot-l" style="color:#fff">Hospitality project name here</div><div class="foot-r">www.verdellresort.com / 06</div>
</section>

<!-- 07 CEO -->
<section class="slide" style="left:100px;top:424px">
  <div class="brand">Verdell</div>
  <div class="panel" style="left:27px;top:20px;width:278px;height:132px;border-radius:66px 0 0 66px"></div>
  <div class="title" style="left:77px;top:37px">Meet Our<br>CEO<span class="bar"></span></div>
  <div class="abs" style="left:75px;top:80px;font-family:'Nunito',sans-serif;font-weight:700;font-size:7px">John M Doe Jr</div>
  <div class="txt" style="left:76px;top:93px;width:82px">Lorem ipsum has been the industry's standard dummy text ever since the 1500s, when an unknown printer took a galley of type and scrambled it to make a type specimen book.</div>
  <div class="social" style="left:76px;top:120px"><span></span><span></span><span></span></div>
  <div class="abs ph-person" style="left:192px;top:34px;width:87px;height:106px" role="img" aria-label="Portrait of the CEO in a dark suit"></div>
  <div class="foot-l">Hospitality project name here</div><div class="foot-r">www.verdellresort.com / 07</div>
</section>

<!-- 08 why invest -->
<section class="slide" style="left:451px;top:424px">
  <div class="brand right">Verdell</div>
  <div class="title" style="left:23px;top:15px">Why Invest with Us ?<span class="bar" style="width:34px"></span></div>
  <div class="panel" style="left:0;top:51px;width:104px;height:121px"></div>
  <div class="opt" style="left:20px;top:66px"><svg class="icon" viewBox="0 0 10 10"><path d="M1 9l1-3 5-5 2 2-5 5z" fill="var(--green)"/></svg><div class="txt" style="width:50px"><span class="lbl">Option One</span>Lorem ipsum has been the industry's standard dummy</div></div>
  <div class="opt" style="left:20px;top:95px"><svg class="icon" viewBox="0 0 10 10"><path d="M0 2h4l1 1h5v6H0z" fill="var(--green)"/></svg><div class="txt" style="width:50px"><span class="lbl">Option Two</span>Lorem ipsum has been the industry's standard dummy</div></div>
  <div class="opt" style="left:20px;top:124px"><svg class="icon" viewBox="0 0 10 10"><rect x="0" y="6" width="2" height="4" fill="var(--green)"/><rect x="4" y="3" width="2" height="7" fill="var(--green)"/><rect x="8" y="0" width="2" height="10" fill="var(--green)"/></svg><div class="txt" style="width:50px"><span class="lbl">Option Three</span>Lorem ipsum has been the industry's standard dummy</div></div>
  <div class="abs ph-night" style="left:104px;top:51px;width:67px;height:121px" role="img" aria-label="Resort villa lit at dusk with a long pool"></div>
  <svg class="abs" style="left:186px;top:55px" width="10" height="90"><circle cx="5" cy="5" r="5" fill="var(--green-soft)"/><circle cx="5" cy="38.5" r="5" fill="var(--green-dark)"/><circle cx="5" cy="72" r="5" fill="var(--green-soft)"/><text x="5" y="6.8" font-size="5" fill="#fff" text-anchor="middle">1</text><text x="5" y="40.3" font-size="5" fill="#fff" text-anchor="middle">2</text><text x="5" y="73.8" font-size="5" fill="#fff" text-anchor="middle">3</text></svg>
  <div class="txt" style="left:208px;top:55px;width:82px"><b>Lorem Ipsum is simply dummy text</b><br>Lorem ipsum has been the industry's standard dummy text ever since the 1500s, when an unknown printer took a galley of type and scrambled to make a type</div>
  <div class="txt" style="left:208px;top:89px;width:82px"><b>Lorem Ipsum is simply dummy text</b><br>Lorem ipsum has been the industry's standard dummy text ever since the 1500s, when an unknown printer took a galley of type and scrambled to make a type</div>
  <div class="txt" style="left:208px;top:122px;width:82px"><b>Lorem Ipsum is simply dummy text</b><br>Lorem ipsum has been the industry's standard dummy text ever since the 1500s, when an unknown printer took a galley of type and scrambled to make a type</div>
  <div class="foot-l">Hospitality project name here</div><div class="foot-r">www.verdellresort.com / 08</div>
</section>

<!-- 09 why invest 2 -->
<section class="slide" style="left:802px;top:424px">
  <div class="brand right">Verdell</div>
  <div class="title" style="left:23px;top:15px">Why Invest with Us ?<span class="bar" style="width:34px"></span></div>
  <div class="txt" style="left:23px;top:41px;width:150px"><b>Lorem Ipsum</b> is simply dummy text of the printing and typesetting industry. Lorem ipsum has been the industry's standard dummy text ever since the 1500s, when an unknown printer took a galley of type and scrambled it to make a type specimen book. It has survived not only five centuries, when an unknown printer took a galley of type and scrambled.</div>
  <div class="abs ph-room" style="left:0;top:74px;width:72px;height:98px" role="img" aria-label="Hotel bedroom with bed and large windows"></div>
  <div class="panel" style="left:72px;top:74px;width:115px;height:98px"></div>
  <div class="abs" style="left:72px;top:122px;width:115px;height:.6px;background:#fff"></div>
  <div class="txt" style="left:85px;top:86px;width:92px"><span class="lbl">Lorem Ipsum</span>Lorem ipsum has been the industry's standard dummy text ever since the 1500s, when an unknown printer took a galley of type and scrambled.</div>
  <div class="txt" style="left:85px;top:132px;width:92px"><span class="lbl">Lorem Ipsum</span>Lorem ipsum has been the industry's standard dummy text ever since the 1500s, when an unknown printer took a galley of type and scrambled.</div>
  <div class="opt" style="left:212px;top:57px"><svg class="icon" viewBox="0 0 10 10"><path d="M1 9l1-3 5-5 2 2-5 5z" fill="var(--green)"/></svg><div class="txt" style="width:50px"><span class="lbl">Option One</span>Lorem ipsum has been the industry's standard dummy</div></div>
  <div class="opt" style="left:212px;top:89px"><svg class="icon" viewBox="0 0 10 10"><path d="M0 2h4l1 1h5v6H0z" fill="var(--green)"/></svg><div class="txt" style="width:50px"><span class="lbl">Option Two</span>Lorem ipsum has been the industry's standard dummy</div></div>
  <div class="opt" style="left:212px;top:119px"><svg class="icon" viewBox="0 0 10 10"><rect x="0" y="6" width="2" height="4" fill="var(--green)"/><rect x="4" y="3" width="2" height="7" fill="var(--green)"/><rect x="8" y="0" width="2" height="10" fill="var(--green)"/></svg><div class="txt" style="width:50px"><span class="lbl">Option Three</span>Lorem ipsum has been the industry's standard dummy</div></div>
  <div class="foot-l">Hospitality project name here</div><div class="foot-r">www.verdellresort.com / 09</div>
</section>

<!-- 10 -->
<section class="slide" style="left:100px;top:612px">
  <div class="brand">Verdell</div>
  <div class="panel" style="left:0;top:81px;width:305px;height:91px"></div>
  <div class="title" style="left:31px;top:26px">Lorem Ipsum is<br>simply dummy text<span class="bar"></span></div>
  <div class="abs ph-resort" style="left:175px;top:0;width:92px;height:81px" role="img" aria-label="Aerial view of resort pools on a cliff by the sea"></div>
  <div class="txt" style="left:28px;top:91px;width:92px"><span class="lbl">Lorem Ipsum</span>Lorem ipsum has been the industry's standard dummy text ever since the 1500s, when an unknown printer took a galley of type and scrambled.</div>
  <div class="opt" style="left:28px;top:124px"><svg class="icon" viewBox="0 0 10 10"><path d="M1 9l1-3 5-5 2 2-5 5z" fill="var(--green)"/></svg><div class="txt" style="width:52px"><span class="lbl">Option One</span>Lorem ipsum has been the industry's standard dummy</div></div>
  <div class="opt" style="left:105px;top:124px"><svg class="icon" viewBox="0 0 10 10"><path d="M0 2h4l1 1h5v6H0z" fill="var(--green)"/></svg><div class="txt" style="width:52px"><span class="lbl">Option Two</span>Lorem ipsum has been the industry's standard dummy</div></div>
  <div class="opt" style="left:182px;top:124px"><svg class="icon" viewBox="0 0 10 10"><rect x="0" y="6" width="2" height="4" fill="var(--green)"/><rect x="4" y="3" width="2" height="7" fill="var(--green)"/><rect x="8" y="0" width="2" height="10" fill="var(--green)"/></svg><div class="txt" style="width:52px"><span class="lbl">Option Three</span>Lorem ipsum has been the industry's standard dummy</div></div>
  <div class="foot-l">Hospitality project name here</div><div class="foot-r">www.verdellresort.com / 10</div>
</section>

<!-- 11 -->
<section class="slide" style="left:451px;top:612px">
  <div class="brand">Verdell</div>
  <div class="panel" style="left:134px;top:0;width:190px;height:172px;border-radius:86px 0 0 86px"></div>
  <div class="title" style="left:31px;top:26px">Lorem Ipsum is<br>simply dummy text<span class="bar"></span></div>
  <div class="txt" style="left:28px;top:72px;width:92px"><span class="lbl">Lorem Ipsum</span>Lorem ipsum has been the industry's standard dummy text ever since the 1500s, when an unknown printer took a galley of type and scrambled.</div>
  <div class="txt" style="left:28px;top:100px;width:92px"><span class="lbl">Lorem Ipsum</span>Lorem ipsum has been the industry's standard dummy text ever since the 1500s, when an unknown printer took a galley of type and scrambled.</div>
  <div class="txt" style="left:28px;top:129px;width:92px"><span class="lbl">Lorem Ipsum</span>Lorem ipsum has been the industry's standard dummy text ever since the 1500s, when an unknown printer took a galley of type and scrambled.</div>
  <div class="opt" style="left:166px;top:33px"><svg class="icon" viewBox="0 0 10 10"><path d="M1 9l1-3 5-5 2 2-5 5z" fill="var(--green)"/></svg><div class="txt" style="width:36px"><span class="lbl">Option One</span>Lorem ipsum has been the industry's standard dummy</div></div>
  <div class="opt" style="left:166px;top:72px"><svg class="icon" viewBox="0 0 10 10"><path d="M0 2h4l1 1h5v6H0z" fill="var(--green)"/></svg><div class="txt" style="width:36px"><span class="lbl">Option Two</span>Lorem ipsum has been the industry's standard dummy</div></div>
  <div class="opt" style="left:166px;top:114px"><svg class="icon" viewBox="0 0 10 10"><rect x="0" y="6" width="2" height="4" fill="var(--green)"/><rect x="4" y="3" width="2" height="7" fill="var(--green)"/><rect x="8" y="0" width="2" height="10" fill="var(--green)"/></svg><div class="txt" style="width:36px"><span class="lbl">Option Three</span>Lorem ipsum has been the industry's standard dummy</div></div>
  <div class="abs ph-pool" style="left:227px;top:26px;width:52px;height:35px" role="img" aria-label="Infinity pool at dusk"></div>
  <div class="abs ph-deck" style="left:227px;top:66px;width:52px;height:35px" role="img" aria-label="Sun loungers on a beach deck"></div>
  <div class="abs ph-resort" style="left:227px;top:108px;width:52px;height:35px" role="img" aria-label="Resort pool overlooking the sea"></div>
  <div class="foot-l">Hospitality project name here</div><div class="foot-r">www.verdellresort.com / 11</div>
</section>

<!-- 12 -->
<section class="slide" style="left:802px;top:612px">
  <div class="brand">Verdell</div>
  <div class="title" style="left:31px;top:26px">Lorem Ipsum is<br>simply dummy text<span class="bar"></span></div>
  <div class="txt" style="left:28px;top:70px;width:125px"><b>Lorem Ipsum</b> is simply dummy text of the printing and typesetting industry. Lorem ipsum has been the industry's standard dummy text ever since the 1500s, when an unknown printer took a galley of type and scrambled it to make a type specimen book. It has survived not only five centuries, but also the</div>
  <div class="panel" style="left:27px;top:84px;width:140px;height:59px;top:96px;height:47px"></div>
  <div class="txt" style="left:38px;top:102px;width:52px"><span class="num">01</span><span class="lbl">Service</span>Lorem ipsum has been the industry's standard dummy</div>
  <div class="txt" style="left:99px;top:102px;width:52px"><span class="num">02</span><span class="lbl">Service</span>Lorem ipsum has been the industry's standard dummy</div>
  <div class="abs ph-dark" style="left:167px;top:29px;width:123px;height:114px" role="img" aria-label="Glass dome building lit at night over water"></div>
  <div class="foot-l">Hospitality project name here</div><div class="foot-r">www.verdellresort.com / 12</div>
</section>

<!-- 13 -->
<section class="slide" style="left:100px;top:800px">
  <div class="abs ph-palm" style="left:0;top:0;width:305px;height:96px" role="img" aria-label="Resort pool with palms and umbrellas"></div>
  <div class="brand">Verdell</div>
  <div class="title" style="left:31px;top:64px;color:#fff">Lorem Ipsum is<br>simply dummy text<span class="bar"></span></div>
  <div class="abs" style="left:209px;top:18px;width:69px;height:154px;background:rgba(233,239,224,.9)"></div>
  <div class="txt" style="left:222px;top:28px;width:50px"><span class="num">01</span><span class="lbl">Service</span>Lorem ipsum has been the industry's standard dummy</div>
  <div class="txt" style="left:222px;top:69px;width:50px"><span class="num">02</span><span class="lbl">Service</span>Lorem ipsum has been the industry's standard dummy</div>
  <div class="txt" style="left:222px;top:107px;width:50px"><span class="num">03</span><span class="lbl">Service</span>Lorem ipsum has been the industry's standard dummy</div>
  <div class="txt" style="left:27px;top:110px;width:165px">Lorem Ipsum is simply dummy text of the printing and typesetting industry. Lorem ipsum has been the industry's standard dummy text ever since the 1500s, when an unknown printer took a galley of type and scrambled it to make a type specimen book. It has survived not only five centuries, but also the leap into electronic typesetting, remaining essentially unchanged. It was popularised in the 1960s with the release of sheets containing passages, and more recently with desktop publishing software including versions of Lorem Ipsum.</div>
  <div class="foot-l">Hospitality project name here</div><div class="foot-r">www.verdellresort.com / 13</div>
</section>

<!-- 14 -->
<section class="slide" style="left:451px;top:800px">
  <div class="brand">Verdell</div>
  <div class="abs ph-desk" style="left:17px;top:29px;width:159px;height:57px" role="img" aria-label="Computer monitor on a dark desk"></div>
  <div class="title" style="left:187px;top:27px">Lorem Ipsum<br>is simply<br>dummy text<span class="bar" style="width:38px"></span></div>
  <div class="panel" style="left:17px;top:95px;width:48px;height:47px"></div>
  <div class="panel" style="left:86px;top:95px;width:48px;height:47px"></div>
  <div class="panel" style="left:155px;top:95px;width:48px;height:47px"></div>
  <div class="panel" style="left:224px;top:95px;width:48px;height:47px"></div>
  <div class="txt" style="left:26px;top:101px;width:38px"><span class="num">01</span><span class="lbl">Service</span>Lorem ipsum has been the industry's standard dummy</div>
  <div class="txt" style="left:95px;top:101px;width:38px"><span class="num">02</span><span class="lbl">Service</span>Lorem ipsum has been the industry's standard dummy</div>
  <div class="txt" style="left:164px;top:101px;width:38px"><span class="num">03</span><span class="lbl">Service</span>Lorem ipsum has been the industry's standard dummy</div>
  <div class="txt" style="left:233px;top:101px;width:38px"><span class="num">04</span><span class="lbl">Service</span>Lorem ipsum has been the industry's standard dummy</div>
  <div class="foot-l">Hospitality project name here</div><div class="foot-r">www.verdellresort.com / 14</div>
</section>

<!-- 15 data slide -->
<section class="slide" style="left:802px;top:800px">
  <div class="brand">Verdell</div>
  <div class="title" style="left:31px;top:35px">Data slide</div>
  <div class="abs" style="left:31px;top:52px;font-size:6px;line-height:1.2;color:var(--body);width:60px">Lorem Ipsum is simply dummy text<span class="bar" style="width:56px"></span></div>
  <div class="txt" style="left:29px;top:89px;width:58px"><b>Lorem Ipsum</b> is simply dummy text of the printing and typesetting industry. Lorem ipsum has been the industry's standard dummy text ever since the 1500s, when an unknown printer took a galley of type and scrambled it to make a type specimen book. It has survived not only five centuries, but also the</div>
  <svg class="abs" style="left:117px;top:35px" width="64" height="64" viewBox="0 0 64 64">
    <circle cx="32" cy="32" r="28" fill="none" stroke="#e6e6e6" stroke-width="4"/>
    <circle cx="32" cy="32" r="28" fill="none" stroke="var(--green-dark)" stroke-width="4" stroke-dasharray="52.8 123.1" transform="rotate(-90 32 32)"/>
    <text x="32" y="36" font-size="10" font-weight="700" text-anchor="middle" fill="#1b1b1b">30%</text>
  </svg>
  <svg class="abs" style="left:201px;top:35px" width="64" height="64" viewBox="0 0 64 64">
    <circle cx="32" cy="32" r="28" fill="none" stroke="#e6e6e6" stroke-width="4"/>
    <circle cx="32" cy="32" r="28" fill="none" stroke="var(--green-soft)" stroke-width="4" stroke-dasharray="35.2 140.7" transform="rotate(-90 32 32)"/>
    <text x="32" y="36" font-size="10" font-weight="700" text-anchor="middle" fill="#1b1b1b">20%</text>
  </svg>
  <div class="txt" style="left:122px;top:112px;width:62px"><span class="lbl" style="font-size:5px">Data title here</span>Lorem ipsum is simply dummy text of the printing and typesetting industry. Lorem ipsum has been</div>
  <div class="txt" style="left:210px;top:112px;width:62px"><span class="lbl" style="font-size:5px">Data title here</span>Lorem ipsum is simply dummy text of the printing and typesetting industry. Lorem ipsum has been</div>
  <div class="foot-l">Hospitality project name here</div><div class="foot-r">www.verdellresort.com / 15</div>
</section>

<!-- 16 sales vs cost -->
<section class="slide" style="left:100px;top:987px">
  <div class="brand">Verdell</div>
  <div class="abs" style="left:45px;top:28px;font-size:7px;color:#555">Sales vs Cost</div>
  <svg class="abs" style="left:20px;top:40px" width="105" height="98" viewBox="0 0 105 98">
    <g stroke="#e2e2e2" stroke-width=".4">
      <line x1="12" y1="8" x2="102" y2="8"/><line x1="12" y1="24" x2="102" y2="24"/><line x1="12" y1="40" x2="102" y2="40"/><line x1="12" y1="56" x2="102" y2="56"/><line x1="12" y1="72" x2="102" y2="72"/><line x1="12" y1="88" x2="102" y2="88"/>
    </g>
    <g font-size="2.6" fill="#777" text-anchor="end"><text x="9" y="9">5</text><text x="9" y="25">4</text><text x="9" y="41">3</text><text x="9" y="57">2</text><text x="9" y="73">1</text><text x="9" y="89">0</text></g>
    <rect x="19" y="19" width="5" height="69" fill="var(--green)"/><rect x="26" y="50" width="5" height="38" fill="#b9dc94"/>
    <rect x="48" y="48" width="5" height="40" fill="var(--green)"/><rect x="55" y="18" width="5" height="70" fill="#b9dc94"/>
    <rect x="77" y="32" width="5" height="56" fill="var(--green)"/><rect x="84" y="59" width="5" height="29" fill="#b9dc94"/>
    <g font-size="2.6" fill="#555" text-anchor="middle"><text x="25" y="93">Category 1</text><text x="54" y="93">Category 2</text><text x="83" y="93">Category 3</text><text x="54" y="97">■ Series 1  ■ Series 2</text></g>
  </svg>
  <div class="panel" style="left:139px;top:29px;width:140px;height:114px"></div>
  <div class="title" style="left:156px;top:50px">Data Slide<span class="bar"></span></div>
  <div class="txt" style="left:153px;top:90px;width:112px">Lorem ipsum has been the industry's standard dummy text ever since the 1500s, when an unknown printer took.<br><br>Lorem ipsum has been the industry's standard dummy text ever since the 1500s, when an unknown printer took.<br><br>Lorem ipsum has been the industry's standard dummy text ever since the 1500s, when an unknown printer took.</div>
  <div class="foot-l">Hospitality project name here</div><div class="foot-r">www.verdellresort.com / 16</div>
</section>

<!-- 17 chart -->
<section class="slide" style="left:451px;top:987px">
  <div class="brand">Verdell</div>
  <div class="abs" style="left:63px;top:28px;font-size:7px;color:#666">Chart Title</div>
  <svg class="abs" style="left:20px;top:40px" width="115" height="100" viewBox="0 0 115 100">
    <g stroke="#e6e6e6" stroke-width=".4"><line x1="10" y1="8" x2="112" y2="8"/><line x1="10" y1="20" x2="112" y2="20"/><line x1="10" y1="32" x2="112" y2="32"/><line x1="10" y1="44" x2="112" y2="44"/><line x1="10" y1="56" x2="112" y2="56"/><line x1="10" y1="68" x2="112" y2="68"/><line x1="10" y1="80" x2="112" y2="80"/></g>
    <g font-size="2.6" fill="#777" text-anchor="end"><text x="7" y="9">14</text><text x="7" y="21">12</text><text x="7" y="33">10</text><text x="7" y="45">8</text><text x="7" y="57">6</text><text x="7" y="69">4</text><text x="7" y="81">0</text></g>
    <polyline points="22,43 46,42 70,45 94,22" fill="none" stroke="#8fca5a" stroke-width=".9"/>
    <polyline points="22,57 46,56 70,59 94,51" fill="none" stroke="#e07a3a" stroke-width=".9"/>
    <polyline points="22,69 46,79 70,73 94,67" fill="none" stroke="#3a78c4" stroke-width=".9"/>
    <g fill="#555"><circle cx="22" cy="43" r=".9"/><circle cx="46" cy="42" r=".9"/><circle cx="70" cy="45" r=".9"/><circle cx="94" cy="22" r=".9"/><circle cx="22" cy="57" r=".9"/><circle cx="46" cy="56" r=".9"/><circle cx="70" cy="59" r=".9"/><circle cx="94" cy="51" r=".9"/><circle cx="22" cy="69" r=".9"/><circle cx="46" cy="79" r=".9"/><circle cx="70" cy="73" r=".9"/><circle cx="94" cy="67" r=".9"/></g>
    <g font-size="2.6" fill="#555" text-anchor="middle"><text x="22" y="86">Category 1</text><text x="46" y="86">Category 2</text><text x="70" y="86">Category 3</text><text x="94" y="86">Category 4</text><text x="58" y="92">— Series 1  — Series 2  — Series 3</text></g>
  </svg>
  <div class="panel" style="left:139px;top:23px;width:140px;height:125px"></div>
  <div class="title" style="left:156px;top:37px">Data Slide</div>
  <div class="txt" style="left:154px;top:56px;width:110px"><b>Lorem Ipsum</b> is simply dummy text of the printing and typesetting industry. Lorem ipsum has been the industry's standard dummy text ever since the 1500s, when an unknown printer took a galley of type and scrambled it to make a type specimen book.</div>
  <svg class="abs" style="left:179px;top:90px" width="44" height="44" viewBox="0 0 44 44">
    <circle cx="22" cy="22" r="18" fill="#fff"/>
    <path d="M22 4a18 18 0 0 1 0 36" fill="none" stroke="var(--green)" stroke-width="2.2"/>
    <text x="22" y="24" font-size="5" font-weight="700" text-anchor="middle" fill="#1b1b1b">100%</text>
  </svg>
  <div class="txt" style="left:236px;top:100px;width:30px;line-height:2.4">Lorem Ipsum<br>Lorem Ipsum<br>Lorem Ipsum<br>Lorem Ipsum</div>
  <div class="foot-l">Hospitality project name here</div><div class="foot-r">www.verdellresort.com / 17</div>
</section>

<!-- 18 contact -->
<section class="slide" style="left:800px;top:987px">
  <div class="abs ph-beach" style="left:0;top:0;width:305px;height:126px" role="img" aria-label="Beach with gentle waves at sunrise"></div>
  <div class="abs" style="left:26px;top:32px;width:139px;height:113px;background:rgba(233,239,224,.9)"></div>
  <div class="abs" style="left:38px;top:16px;display:flex;align-items:center;gap:3px;font-family:'Nunito',sans-serif;font-weight:900;font-size:9px;color:var(--green-dark)">
    <span style="width:18px;height:18px;border-radius:50%;background:var(--green)"></span>Verdell
  </div>
  <div class="title" style="left:42px;top:55px">Contact Us</div>
  <div class="txt" style="left:39px;top:88px;width:120px;line-height:1.5">
    <div style="display:flex;gap:14px;margin-bottom:5px"><b style="width:24px">Address</b><span>Lorem ipsum has been the industry's standard dummy text ever since the 1500s.</span></div>
    <div style="display:flex;gap:14px;margin-bottom:5px"><b style="width:24px">Phone</b><span>+123 456 789</span></div>
    <div style="display:flex;gap:14px"><b style="width:24px">Website</b><span>www.yourwebsite.com</span></div>
  </div>
  <div class="social" style="left:78px;top:133px"><span></span><span></span><span></span></div>
  <div class="foot-l">Hospitality project name here</div><div class="foot-r">www.verdellresort.com / 18</div>
</section>

</body>
</html>
```